Business card design for holistic health care clinic

We need a double-sided business card design for our holistic health care clinic that integrates our logo design and also its color scheme. My business is called Valmira. It is an integrative medicine clinic. You have already done the logo for me. Please ensure an elegant and upscale design that is not cluttered, but still has all the necessary information (please see below for details).

Target Market(s)

Wellness, fitness, rehabilitation for educated, well-traveled open-minded clients who are focused on natural, organic, balanced and preventive healthcare and lifestyle.

Industry/Entity Type

Medical

Contact Information for Business Card

Modern, clean.

Number of Pages Required

1 page

Font styles to use
Serif
Sans Serif

Colors

Designer to choose colors to be used in the design.

Requirements
Must have
• Logo on one side, all other information on the other side.
• Other information should include:
• Tobias Wrenfeld - DOE, CPT, LMT
• 4100 East Marrow Drive
• Austin, TX 78119
• 512 555 0148
• 818 555 0192
• info@ValmiraHealth.example
• t.wrenfeld@ValmiraHealth.example
Nice to have
• Darker background on front - but not totally black - shaded/dark gray.

```html
<!DOCTYPE html>
<html lang="en">
<head>
<meta charset="utf-8">
<title>Valmira Business Card</title>
<link rel="stylesheet" href="https://fonts.googleapis.com/css2?family=Montserrat:wght@600;700&family=Nunito:wght@700&family=Work+Sans:wght@400&display=swap">
<style>
  :root {
    --brand-blue: #1a93d0;
    --ink-dark: #2b2b2b;
    --text-gray: #333333;
    --card-white: #ffffff;
    --backdrop: #2a2a2a;
  }
  * { margin: 0; padding: 0; box-sizing: border-box; }
  html, body { width: 1200px; height: 930px; overflow: hidden; background: var(--backdrop); }
  .canvas { position: relative; width: 1200px; height: 930px; }

  .card { position: absolute; left: 278px; width: 645px; height: 368px; border-radius: 22px; overflow: hidden; }
  .card-front { top: 76px; background: var(--card-white); }
  .card-back { top: 486px; background: var(--brand-blue); }

  .wordmark { font-family: "Montserrat", sans-serif; font-weight: 700; letter-spacing: 0.5px; line-height: 1; }
  .tagline { font-family: "Nunito", sans-serif; font-weight: 700; line-height: 1; }

  .front-brand { position: absolute; left: 34px; top: 62px; color: var(--brand-blue); }
  .front-brand .wordmark { font-size: 54px; }
  .front-brand .tagline { font-size: 17px; margin-top: 8px; margin-left: 4px; }

  .holder { position: absolute; right: 36px; top: 186px; text-align: right; }
  .holder-name { font-family: "Montserrat", sans-serif; font-weight: 600; font-size: 29px; color: var(--brand-blue); line-height: 1; letter-spacing: -0.3px; }
  .holder-credentials { font-family: "Work Sans", sans-serif; font-size: 16px; color: var(--text-gray); margin-top: 5px; }
  .divider { position: absolute; left: 34px; top: 224px; width: 458px; height: 2px; background: var(--brand-blue); }

  .edge-mark-dark { position: absolute; left: 626px; top: 202px; width: 5px; height: 42px; background: var(--ink-dark); }
  .edge-mark-blue { position: absolute; left: 633px; top: 202px; width: 12px; height: 42px; background: var(--brand-blue); }

  .contact-list { position: absolute; left: 34px; top: 246px; list-style: none; font-family: "Work Sans", sans-serif; font-size: 16px; color: var(--text-gray); }
  .contact-list li { display: flex; align-items: center; height: 20.3px; }
  .contact-list svg { width: 12px; height: 12px; margin-right: 10px; margin-left: 2px; flex: none; }

  .address { position: absolute; right: 40px; top: 266px; text-align: right; font-family: "Work Sans", sans-serif; font-size: 16px; color: var(--text-gray); line-height: 20.3px; }

  .footer-band { position: absolute; left: 0; bottom: 0; width: 645px; height: 40px; }

  .back-brand { position: absolute; left: 0; right: 0; top: 145px; text-align: center; color: var(--card-white); }
  .back-brand .wordmark { font-size: 86px; }
  .back-brand .tagline { font-size: 26px; margin-top: 14px; }
</style>
</head>
<body>
<main class="canvas">

  <section class="card card-front" aria-label="Card front with contact details">
    <div class="front-brand">
      <div class="wordmark">VALMIRA</div>
      <div class="tagline">Integrative Holistic Medicine</div>
    </div>

    <div class="holder">
      <div class="holder-name">TOBIAS WRENFELD</div>
      <div class="holder-credentials">DOE, CPT, LMT</div>
    </div>
    <div class="divider"></div>
    <div class="edge-mark-dark"></div>
    <div class="edge-mark-blue"></div>

    <ul class="contact-list">
      <li>
        <svg viewBox="0 0 12 12"><path d="M3 1 L5 3.5 L4 5 C4.8 6.8 5.6 7.6 7 8 L8.5 7 L11 9 L9.5 11 C5 10.5 1.5 7 1 2.5 Z" fill="var(--brand-blue)"/></svg>
        512 555 0148
      </li>
      <li>
        <svg viewBox="0 0 12 12"><rect x="3" y="0.8" width="6" height="10.4" rx="1" fill="none" stroke="var(--brand-blue)" stroke-width="1.4"/><circle cx="6" cy="9.2" r="0.7" fill="var(--brand-blue)"/></svg>
        818 555 0192
      </li>
      <li>
        <svg viewBox="0 0 12 12"><rect x="0.8" y="2.5" width="10.4" height="7" fill="none" stroke="var(--brand-blue)" stroke-width="1.2"/><path d="M1 3 L6 6.8 L11 3" fill="none" stroke="var(--brand-blue)" stroke-width="1.2"/></svg>
        info@ValmiraHealth.example
      </li>
      <li>
        <svg viewBox="0 0 12 12"><circle cx="6" cy="6" r="5" fill="none" stroke="var(--brand-blue)" stroke-width="1"/><ellipse cx="6" cy="6" rx="2.2" ry="5" fill="none" stroke="var(--brand-blue)" stroke-width="0.9"/><path d="M1 6 H11 M2 3.5 H10 M2 8.5 H10" stroke="var(--brand-blue)" stroke-width="0.9"/></svg>
        t.wrenfeld@ValmiraHealth.example
      </li>
    </ul>

    <address class="address" style="font-style: normal;">
      4100 East Marrow Drive<br>
      Austin, TX 78119
    </address>

    <svg class="footer-band" viewBox="0 0 645 40" preserveAspectRatio="none">
      <path d="M0 13 L352 13 C362 13 366 16 360 19 L0 19 Z" fill="var(--ink-dark)"/>
      <path d="M0 27 L360 27 C380 27 392 12 420 12 L645 12 L645 40 L0 40 Z" fill="var(--brand-blue)"/>
    </svg>
  </section>

  <section class="card card-back" aria-label="Card back with brand name">
    <div class="back-brand">
      <div class="wordmark">VALMIRA</div>
      <div class="tagline">Integrative Holistic Medicine</div>
    </div>
  </section>

</main>
</body>
</html>
```